Business card for a Exhibition booth fabrication company

Hi. My company would like to change our corporate name card. We are an events and Exhibition stand builder company. We would like our corporate name card to resonate what we do. I need someone to create something unique that relates to the industry that I am in. The graphic designer should be creative to incorporate the elements of my industry and try to blend in well in the design of the card. Our aim is to ensure that we are unique and our card can look different from our competitors.
Updates

Target Market(s)

Marketing and events manager from all companies

Contact Information for Business Card

The business card should have the following details:
Name
Job Title
Email
Website

Colors

Designer to choose colors to be used in the design.

Requirements
Must have
• The card must be look something that is relevant to the service that I am providing. My website is: www.velmora-buildworks.com
• You can see my website to get more information on what service that I am doing
Nice to have
• On the back of my card, I would like to have a globe image with the incorporation of my company logo. This is to indicate that my services can be done in any part of the world.

```html
<!DOCTYPE html>
<html lang="en">
<head>
<meta charset="utf-8">
<title>Velmora Buildworks – Business Card</title>
<link href="https://fonts.googleapis.com/css2?family=Michroma&family=Open+Sans:wght@400;600&display=swap" rel="stylesheet">
<style>
  :root {
    --canvas-bg: #2b2b2c;
    --card-bg: #1e1f21;
    --card-edge: #2a2b2e;
    --accent-red: #e3101f;
    --text-light: #e6e6e6;
    --text-muted: #bdbdbd;
    --rule: #5a5a5c;
    --pattern-top: #2c2d30;
  }
  html, body {
    margin: 0;
    padding: 0;
    width: 1200px;
    height: 1108px;
    overflow: hidden;
    background: var(--canvas-bg);
  }
  .canvas {
    position: relative;
    width: 1200px;
    height: 1108px;
  }
  .card {
    position: absolute;
    top: 236px;
    width: 400px;
    height: 636px;
    border-radius: 22px;
    background: var(--card-bg);
    box-shadow: 0 0 0 1px var(--card-edge);
    overflow: hidden;
  }
  .card--front { left: 170px; }
  .card--back { left: 630px; }

  /* Front */
  .brand {
    position: absolute;
    top: 150px;
    left: 0;
    right: 0;
    text-align: center;
  }
  .brand__name {
    font-family: "Michroma", sans-serif;
    font-size: 19px;
    letter-spacing: 2px;
    color: var(--text-light);
    text-transform: uppercase;
  }
  .contact {
    position: absolute;
    right: 36px;
    bottom: 74px;
    text-align: right;
    font-family: "Open Sans", sans-serif;
  }
  .contact__name {
    font-family: "Michroma", sans-serif;
    font-size: 23px;
    color: var(--accent-red);
    text-transform: uppercase;
    letter-spacing: 0.5px;
    line-height: 1.1;
  }
  .contact__title {
    font-size: 17px;
    color: var(--text-light);
    margin-top: 2px;
  }
  .contact__rule {
    width: 210px;
    height: 1px;
    background: var(--rule);
    margin: 12px 0 10px auto;
  }
  .contact__line {
    font-size: 16px;
    color: var(--text-light);
    line-height: 1.45;
  }
  .contact__label {
    color: var(--accent-red);
    font-weight: 600;
  }
  .contact__region { color: var(--accent-red); }
  .contact__web { color: var(--accent-red); font-size: 16px; line-height: 1.45; }

  /* Back */
  .monogram-field {
    position: absolute;
    top: 0;
    left: 0;
    right: 0;
    height: 470px;
    background: linear-gradient(to bottom, var(--pattern-top), var(--card-bg));
  }
  .services {
    position: absolute;
    left: 0;
    right: 0;
    bottom: 56px;
    margin: 0;
    padding: 0;
    list-style: none;
    text-align: center;
    font-family: "Open Sans", sans-serif;
    font-size: 17px;
    line-height: 1.38;
    color: var(--text-light);
  }
</style>
</head>
<body>
<main class="canvas">
  <section class="card card--front" aria-label="Card front">
    <div class="brand">
      <div class="brand__name">Velmora Buildworks</div>
    </div>
    <div class="contact">
      <div class="contact__name">Daniel Harlow</div>
      <div class="contact__title">Managing Director</div>
      <div class="contact__rule"></div>
      <div class="contact__line"><span class="contact__label">P:</span> +65 81472036 <span class="contact__region">(Singapore)</span></div>
      <div class="contact__line"><span class="contact__label">P:</span> +974 55289141 <span class="contact__region">(Qatar)</span></div>
      <div class="contact__line"><span class="contact__label">E:</span> info@www.velmora-buildworks.com</div>
      <div class="contact__web">www.velmora-buildworks.com</div>
    </div>
  </section>

  <section class="card card--back" aria-label="Card back">
    <div class="monogram-field" role="img" aria-label="Faint repeating brand monogram pattern fading toward the bottom"></div>
    <ul class="services">
      <li>Exhibition Booth Fabrication</li>
      <li>Outdoor Booth Setup</li>
      <li>Interior Design</li>
      <li>Installation and Dismantle</li>
      <li>Exhibition Management</li>
      <li>Shell Scheme Display Booth</li>
      <li>Custom Stand Design</li>
      <li>Exhibition Furniture and Equipment</li>
      <li>Exhibition Project Management</li>
    </ul>
  </section>
</main>
</body>
</html>
```